Personal Motivational Quote Poster Design

I would like to create a poster with some of my favorite quotes to hang in my office. I did similar projects in 2012 and 2014. I've uploaded the winning designs so you can get a better idea of what I'm looking for. I will provide feedback on your design within 24 hours of receiving it.

The poster must contain the following quotes:

“What the pupil must learn, if he learns anything at all, is that the world will do most of the work for you, provided you cooperate with it by identifying how it really works and aligning with those realities. If we do not let the world teach us, it teaches us a lesson.” - Harold Quenby

“I tackle every big new problem by asking two questions: Who has dealt with this problem well? And what can we learn from them?” - Walt Prisco

“If we can really understand the problem, the answer will come out of it, because the answer is not separate from the problem.” - Ravindra Selvapathi

“Success is nothing more than a few simple disciplines, practiced every day; while failure is simply a few errors in judgment, repeated every day. It is the accumulative weight of our disciplines and our judgments that leads us to either fortune or failure.” - Ned Falco

“Inaction breeds doubt and fear. Action breeds confidence and courage.” - Rufus Pembrook

“What’s the one thing you can do, such that by doing it, everything else will be easier or unnecessary?” - Lyle Dorsey

Requirements
Must have
• The poster will be 24" high x 36" long and printed on canvas, so the image you create needs to have a resolution of at least 2700 x 3900.
Nice to have
• I don't have an exact vision for how the poster should look, so I am totally open to you using your creativity to develop, arrange and present the content as you'd like.

That said, I would like an image (photo or posterized image) of the person being quoted along with each quote. I do not have specific images that I would like you to use, so you will need to find the images on your own.

The images don't need to be perfect... I am more interested in the poster relating the essence of the quotes and the people being quoted than I am in perfect photographic images of the people being quoted.

```html
<!DOCTYPE html>
<html lang="en">
<head>
<meta charset="utf-8">
<title>Quotes Poster</title>
<link href="https://fonts.googleapis.com/css2?family=Open+Sans:ital,wght@0,400;0,600;0,700;0,800;1,400;1,600;1,700&family=Mr+Dafoe&display=swap" rel="stylesheet">
<style>
:root{
  --paper:#ebe8dc;
  --paper-line:#dfdbcd;
  --blue:#3f4b7c;
  --green:#6f9a3d;
  --purple:#693f80;
  --orange:#b3642f;
  --magenta:#983a63;
  --teal:#3e8a7d;
  --ink:#ffffff;
  --ink-dark:#1d2340;
  --highlight:#cfe7f8;
}
*{margin:0;padding:0;box-sizing:border-box}
html,body{width:848px;height:1200px;overflow:hidden}
body{
  position:relative;
  font-family:"Open Sans",Arial,sans-serif;
  color:var(--ink);
  background:repeating-linear-gradient(180deg,var(--paper) 0 14px,var(--paper-line) 14px 15px);
}
.banner{
  position:absolute;
  overflow:hidden;
  clip-path:polygon(0 4%,3% 2%,6% 5%,9% 1%,13% 4%,17% 0,21% 4%,26% 2%,30% 5%,35% 1%,40% 4%,45% 0,50% 4%,55% 2%,60% 4%,65% 0,70% 4%,75% 1%,80% 5%,85% 2%,90% 4%,95% 0,100% 3%,99% 20%,100% 35%,98% 50%,100% 65%,99% 80%,100% 97%,95% 100%,90% 96%,85% 99%,80% 96%,75% 100%,70% 96%,65% 99%,60% 95%,55% 99%,50% 96%,45% 100%,40% 96%,35% 99%,30% 95%,25% 99%,20% 96%,15% 100%,10% 96%,5% 99%,0 96%,1% 80%,0 65%,2% 50%,0 35%,1% 20%);
}
.portrait{position:absolute;top:0;bottom:0}
.banner--blue{left:68px;top:16px;width:758px;height:204px;background:var(--blue)}
.banner--blue .portrait{right:10px;width:219px;background:linear-gradient(160deg,#8d8f98,#55586a)}
.banner--green{left:26px;top:209px;width:549px;height:214px;background:var(--green)}
.banner--green .portrait{right:3px;width:232px;background:linear-gradient(160deg,#a6ba86,#7f9a5d)}
.banner--purple{left:34px;top:423px;width:789px;height:212px;background:var(--purple)}
.banner--purple .portrait{right:3px;width:235px;background:linear-gradient(160deg,#a792b4,#3d2c4c)}
.banner--orange{left:209px;top:617px;width:598px;height:214px;background:var(--orange)}
.banner--orange .portrait{right:2px;width:199px;background:linear-gradient(160deg,#d4a27c,#8a5732)}
.banner--magenta{left:24px;top:836px;width:598px;height:172px;background:var(--magenta);transform:rotate(-3deg)}
.banner--magenta .portrait{right:0;width:152px;background:linear-gradient(160deg,#c58aa5,#6d2b48)}
.banner--teal{left:185px;top:978px;width:609px;height:246px;background:var(--teal);transform:rotate(-5deg)}
.banner--teal .portrait{right:10px;width:157px;background:linear-gradient(160deg,#8cb8b0,#356e64)}

.quote{position:absolute;white-space:nowrap;line-height:1}
.quote > .line{display:block;position:absolute;white-space:nowrap}
.caps{text-transform:uppercase;font-weight:700}
.em{font-style:italic;font-weight:700}
.soft{font-style:italic}
.upper{font-size:13px}
.mark{background:var(--highlight);color:var(--ink-dark);padding:1px 4px}
.signature{
  position:absolute;font-family:"Mr Dafoe",cursive;color:var(--ink);
  white-space:nowrap;line-height:1;word-spacing:5px;
}
.signature::after{content:"";display:block;height:2px;width:70%;margin:2px 0 0 8%;background:rgba(255,255,255,.75)}

.quote--blue{left:112px;top:88px;font-size:13px;transform:rotate(-3deg);transform-origin:left top}
.quote--green{left:76px;top:272px;font-size:17px}
.quote--purple{left:91px;top:480px;font-size:12px}
.quote--orange{left:272px;top:672px;transform:rotate(2deg);transform-origin:left top}
.quote--magenta{left:57px;top:900px;transform:rotate(-3deg);transform-origin:left top}
.quote--teal{left:253px;top:1045px;transform:rotate(-6deg);transform-origin:left top}
</style>
</head>
<body>

<div class="banner banner--blue"><div class="portrait" role="img" aria-label="Portrait of Harold Quenby"></div></div>
<div class="banner banner--green"><div class="portrait" role="img" aria-label="Portrait of Walt Prisco"></div></div>
<div class="banner banner--purple"><div class="portrait" role="img" aria-label="Portrait of Ned Falco"></div></div>
<div class="banner banner--orange"><div class="portrait" role="img" aria-label="Portrait of Ravindra Selvapathi"></div></div>
<div class="banner banner--magenta"><div class="portrait" role="img" aria-label="Portrait of Rufus Pembrook"></div></div>
<div class="banner banner--teal"><div class="portrait" role="img" aria-label="Portrait of Lyle Dorsey"></div></div>

<div class="quote quote--blue">
  <span class="line" style="top:0;left:0">“What the pupil must learn, <b class="em">if he learns anything at all,</b></span>
  <span class="line" style="top:19px;left:4px">is that the world will do most of the work for you,</span>
  <span class="line caps mark" style="top:38px;left:0;font-size:14px">Provided you cooperate with it</span>
  <span class="line" style="top:58px;left:4px;font-size:12px">by identifying how it really works and aligning with those realities.</span>
  <span class="line mark" style="top:75px;left:0">If we do not let the world teach us, it teaches us a lesson.”</span>
</div>
<div class="signature" style="left:545px;top:154px;font-size:30px;transform:rotate(-3deg)">Harold Quenby</div>

<div class="quote quote--green">
  <span class="line" style="top:0;left:0">“I tackle every big new problem by</span>
  <span class="line caps" style="top:27px;left:0;font-size:18px">Asking two questions:</span>
  <span class="line em" style="top:58px;left:0;font-size:14px">Who has dealt with this problem well?</span>
  <span class="line em" style="top:86px;left:0;font-size:14px">And what can we learn from them?”</span>
</div>
<div class="signature" style="left:350px;top:366px;font-size:28px">Walt Prisco</div>

<div class="quote quote--purple">
  <span class="line" style="top:0;left:0"><b class="caps">“Success</b> <i>is nothing more than a few simple disciplines, practiced every day;</i> while</span>
  <span class="line" style="top:24px;left:0"><b class="caps">Failure</b> <i>is simply a few errors in judgment, repeated every day.</i> It is the accumulative</span>
  <span class="line" style="top:50px;left:0">weight of <b class="upper" style="font-weight:400">OUR DISCIPLINES</b> and <b class="upper" style="font-weight:400">OUR JUDGMENTS</b></span>
  <span class="line" style="top:73px;left:0;font-size:13px;font-weight:600">that leads us to either fortune or failure.”</span>
</div>
<div class="signature" style="left:548px;top:560px;font-size:28px">Ned Falco</div>

<div class="quote quote--orange">
  <span class="line" style="top:0;left:0;font-size:13px">“If we can really understand the problem,</span>
  <span class="line soft" style="top:28px;left:0;font-size:17px">the answer will come out of it,</span>
  <span class="line caps" style="top:58px;left:0;font-size:16px">Because the answer is not</span>
  <span class="line caps em" style="top:84px;left:0;font-size:16px">Separate from the problem.”</span>
</div>
<div class="signature" style="left:455px;top:786px;font-size:27px;transform:rotate(2deg)">Ravindra Selvapathi</div>

<div class="quote quote--magenta">
  <span class="line" style="top:0;left:0;font-size:19px"><b class="caps">“Inaction</b> breeds <b class="em">doubt and fear</b>.</span>
  <span class="line" style="top:30px;left:0;font-size:19px"><b class="caps">Action</b> breeds <b class="em">confidence and courage</b>.”</span>
</div>
<div class="signature" style="left:347px;top:940px;font-size:29px;transform:rotate(-3deg)">Rufus Pembrook</div>

<div class="quote quote--teal">
  <span class="line" style="top:0;left:0;font-size:17px">“What’s the one thing you can do,</span>
  <span class="line caps" style="top:26px;left:0;font-size:20px">Such that by doing it,</span>
  <span class="line" style="top:54px;left:0;font-size:17px">everything else will be</span>
  <span class="line caps" style="top:80px;left:0;font-size:20px">Easier or unnecessary?”</span>
</div>
<div class="signature" style="left:564px;top:1106px;font-size:28px;transform:rotate(-6deg)">Lyle Dorsey</div>

</body>
</html>
```